Cards
Hollowmere Estate Advisors
Project: Cards
Cards - Real Estate
Creative Brief
Modern
Teodoro Villanueva
Managing Broker
487 Quarry Ln. Munster IN 46390
homesbytv@brindlepost.net
I also need the Dwellcor/HXR logo, along with the Open Hearth logo

```html
<!DOCTYPE html>
<html lang="en">
<head>
<meta charset="utf-8">
<title>Hollowmere Estate Advisors – Business Card</title>
<link rel="stylesheet" href="https://fonts.googleapis.com/css2?family=Cinzel:wght@500&family=Tinos:wght@400;700&display=swap">
<style>
  :root {
    --page-bg: #2b2b2b;
    --card-white: #ffffff;
    --brand-green: #5e9a1f;
    --brand-blue: #1f6fb8;
    --ink-navy: #1d3b5c;
    --ink-dark: #2a2a2a;
    --badge-grey: #4a4a4a;
    --divider: #9a9a9a;
  }
  html, body {
    margin: 0;
    padding: 0;
    width: 1200px;
    height: 780px;
    overflow: hidden;
    background: var(--page-bg);
  }
  .card {
    position: absolute;
    left: 75px;
    top: 90px;
    width: 1050px;
    height: 600px;
    background: var(--card-white);
    border-radius: 34px;
    overflow: hidden;
    box-shadow: 0 18px 40px rgba(0,0,0,0.45);
    font-family: "Tinos", "Times New Roman", serif;
  }
  .card-swoosh {
    position: absolute;
    inset: 0;
    width: 1050px;
    height: 600px;
  }
  .partner-badges {
    position: absolute;
    top: 44px;
    left: 788px;
    display: flex;
    gap: 12px;
    align-items: flex-end;
  }
  .partner-badge {
    background: var(--badge-grey);
  }
  .partner-badge--dwellcor { width: 30px; height: 38px; }
  .partner-badge--hxr { width: 58px; height: 38px; }
  .partner-badge--hearth { width: 36px; height: 38px; }

  .brand {
    position: absolute;
    left: 150px;
    top: 196px;
    display: flex;
    align-items: center;
    gap: 22px;
  }
  .brand-mark {
    width: 86px;
    height: 86px;
    border-radius: 50%;
    background: var(--brand-blue);
  }
  .brand-name {
    font-family: "Cinzel", "Times New Roman", serif;
    font-weight: 500;
    color: var(--ink-navy);
    font-size: 40px;
    line-height: 1.08;
    letter-spacing: 1px;
    margin: 0;
  }

  .agent {
    position: absolute;
    right: 620px;
    top: 378px;
    text-align: right;
  }
  .agent-name {
    margin: 0;
    color: var(--brand-green);
    font-weight: 700;
    font-size: 30px;
  }
  .agent-title {
    margin: 2px 0 14px;
    color: var(--brand-blue);
    font-size: 22px;
  }
  .agent-address {
    font-style: normal;
    color: var(--ink-dark);
    font-size: 22px;
    line-height: 1.3;
  }

  .divider {
    position: absolute;
    left: 456px;
    top: 372px;
    width: 2px;
    height: 166px;
    background: var(--divider);
  }

  .contact-list {
    position: absolute;
    left: 474px;
    top: 372px;
    margin: 0;
    padding: 0;
    list-style: none;
    color: var(--ink-dark);
    font-size: 22px;
  }
  .contact-item {
    display: flex;
    align-items: center;
    gap: 12px;
    height: 38px;
  }
  .contact-icon {
    width: 20px;
    height: 20px;
    fill: var(--brand-green);
  }
</style>
</head>
<body>
  <main class="card">
    <svg class="card-swoosh" viewBox="0 0 1050 600" aria-hidden="true">
      <path d="M760 0 Q930 70 1050 230 L1050 0 Z" fill="var(--brand-green)"/>
      <path d="M730 0 Q915 80 1050 265" fill="none" stroke="var(--brand-blue)" stroke-width="6"/>
      <path d="M0 330 Q90 520 300 600 L0 600 Z" fill="var(--brand-green)"/>
      <path d="M0 300 Q95 525 335 600" fill="none" stroke="var(--brand-blue)" stroke-width="6"/>
    </svg>

    <div class="partner-badges">
      <div class="partner-badge partner-badge--dwellcor" role="img" aria-label="Dwellcor badge"></div>
      <div class="partner-badge partner-badge--hxr" role="img" aria-label="HXR badge"></div>
      <div class="partner-badge partner-badge--hearth" role="img" aria-label="Open Hearth badge"></div>
    </div>

    <header class="brand">
      <div class="brand-mark" aria-hidden="true"></div>
      <h1 class="brand-name">Hollowmere<br>Estate Advisors</h1>
    </header>

    <section class="agent">
      <h2 class="agent-name">Teodoro Villanueva</h2>
      <p class="agent-title">Managing Broker</p>
      <address class="agent-address">487 Quarry Ln.<br>Munster IN 46390</address>
    </section>

    <div class="divider"></div>

    <ul class="contact-list">
      <li class="contact-item">
        <svg class="contact-icon" viewBox="0 0 20 20" aria-hidden="true"><path d="M4 1 L8 1 L9 6 L6.5 7.5 Q8 12 12.5 13.5 L14 11 L19 12 L19 16 Q19 19 16 19 Q2 17 1 4 Q1 1 4 1 Z"/></svg>
        <span>773-555-0184</span>
      </li>
      <li class="contact-item">
        <svg class="contact-icon" viewBox="0 0 20 20" aria-hidden="true"><path d="M5 0 H15 Q16 0 16 1 V19 Q16 20 15 20 H5 Q4 20 4 19 V1 Q4 0 5 0 Z M6 3 V15 H14 V3 Z"/></svg>
        <span>773-555-0127</span>
      </li>
      <li class="contact-item">
        <svg class="contact-icon" viewBox="0 0 20 20" aria-hidden="true"><path d="M5 1 H13 V6 H5 Z M2 7 H18 V16 H15 V19 H5 V16 H2 Z M7 13 V17 H13 V13 Z"/></svg>
        <span>773-555-0163</span>
      </li>
      <li class="contact-item">
        <svg class="contact-icon" viewBox="0 0 20 20" aria-hidden="true"><path d="M1 4 H19 V16 H1 Z M2.5 5.5 L10 11 L17.5 5.5 Z" fill-rule="evenodd"/></svg>
        <span>homesbytv@brindlepost.net</span>
      </li>
    </ul>
  </main>
</body>
</html>
```